Need webdesign for service company that provides Car hiring service and transit service

We need a web design for a company that provides airport transit services and transport services including Limo, Corporate cars, Disability transit, Family transit service. We need is a simple and professional design.

Below is site which we like and also offer the same service http://www.ridelarkway.com.au/
Updates

Project Deadline Extended
Reason: Waiting for the Feedback from multiple stakeholders. Need the time to select and approve the design

Target Market(s)

Tourism, Travel

Industry/Entity Type

Airport

Number of Pages Required

3 page

Font styles to use
Decorative
Script

Requirements
Must have
• Simple and Professional, Site we like http://www.ridelarkway.com.au/ and also need to mobile friendly
Should not have
• Shouldn't have too many images

```html
<!DOCTYPE html>
<html lang="en">
<head>
<meta charset="utf-8">
<title>Tranzly – Private and Business Transport</title>
<link href="https://fonts.googleapis.com/css2?family=Open+Sans:wght@400;600;700&display=swap" rel="stylesheet">
<style>
  :root {
    --white: #ffffff;
    --ink: #1a1a1a;
    --text: #333333;
    --orange: #e07b00;
    --orange-soft: #e89a1c;
    --hero-dark: #1d1a1c;
    --footer-bg: #e0e0e0;
    --field-bg: #f4f4f4;
  }
  * { box-sizing: border-box; margin: 0; padding: 0; }
  html, body { width: 1200px; height: 960px; overflow: hidden; }
  body { font-family: "Open Sans", Arial, sans-serif; color: var(--text); background: var(--white); position: relative; }

  .site-header { position: absolute; left: 0; top: 0; width: 1200px; height: 111px; background: var(--white); }
  .brand { position: absolute; left: 100px; top: 36px; display: flex; align-items: center; gap: 10px; }
  .brand-mark { width: 30px; height: 30px; border: 2px solid var(--ink); }
  .brand-name { font-size: 30px; font-weight: 600; color: var(--ink); letter-spacing: 0.5px; line-height: 1; }
  .header-actions { position: absolute; top: 34px; left: 936px; display: flex; gap: 15px; }
  .icon-btn { width: 45px; height: 45px; border: 2.5px solid var(--ink); border-radius: 50%; display: flex; align-items: center; justify-content: center; }

  .hero { position: absolute; left: 0; top: 111px; width: 1200px; height: 577px;
    background:
      linear-gradient(125deg, rgba(60,20,10,.9) 0%, rgba(110,55,25,.6) 30%, rgba(40,35,40,.7) 55%, rgba(20,50,55,.75) 80%, rgba(20,30,40,.9) 100%),
      var(--hero-dark); }
  .hero-title { position: absolute; top: 38px; width: 100%; text-align: center; color: var(--white); font-size: 29px; font-weight: 700; }
  .hero-sub { position: absolute; top: 87px; width: 100%; text-align: center; color: var(--white); font-size: 17px; }

  .quote-box { position: absolute; left: 99px; top: 152px; width: 377px; height: 380px; border: 2px solid rgba(255,255,255,.85); background: rgba(60,50,50,.55); }
  .quote-title { position: absolute; left: 20px; top: 44px; color: var(--white); font-size: 22px; font-weight: 700; }
  .quote-rule { position: absolute; left: 22px; top: 92px; width: 162px; height: 2px; background: var(--white); }
  .field { position: absolute; left: 22px; width: 332px; height: 41px; background: var(--field-bg); font-size: 14px; color: var(--ink); padding: 0 10px; line-height: 41px; }
  .field.origin { top: 140px; }
  .field.destination { top: 200px; }
  .estimate-btn { position: absolute; left: 22px; top: 268px; width: 191px; height: 58px; background: var(--orange); color: var(--white); font-size: 21px; font-weight: 700; line-height: 58px; text-align: center; }

  .service { position: absolute; border: 2px solid rgba(255,255,255,.9); overflow: hidden; }
  .service-photo { position: absolute; inset: 0; }
  .service-name { position: absolute; left: 16px; bottom: 16px; color: var(--white); font-weight: 700; font-size: 24px; letter-spacing: .3px; }
  .service.small .service-name { font-size: 19px; left: 11px; bottom: 10px; }
  .corporate { left: 498px; top: 152px; width: 308px; height: 141px; }
  .corporate .service-photo { background: linear-gradient(120deg, #e39a2a, #d98409 60%, #c97300); }
  .disability { left: 498px; top: 318px; width: 308px; height: 214px; background: linear-gradient(135deg, #3f8a72 0%, #6e8a6a 45%, #8a7560 75%, #9a5a48 100%); }
  .disability .pin { position: absolute; left: 16px; top: 62px; }
  .family { left: 829px; top: 152px; width: 273px; height: 224px; }
  .family .service-photo { background: linear-gradient(160deg, #5e7a66 0%, #8fa2a8 45%, #c9ccd2 75%, #6a6e78 100%); }
  .airport { left: 829px; top: 401px; width: 273px; height: 131px; }
  .airport .service-photo { background: linear-gradient(120deg, #eea53a, #e68f16 55%, #d47d06); }

  .features { position: absolute; left: 0; top: 688px; width: 1200px; height: 221px; }
  .feature { position: absolute; top: 46px; width: 300px; text-align: center; }
  .feature svg { display: block; margin: 0 auto; }
  .feature p { margin-top: 23px; font-size: 14px; line-height: 20.5px; color: var(--text); }
  .feature.one { left: 92px; }
  .feature.two { left: 450px; }
  .feature.three { left: 810px; }

  .site-footer { position: absolute; left: 0; top: 909px; width: 1200px; height: 51px; background: var(--footer-bg); text-align: center; line-height: 51px; font-size: 14px; color: var(--text); }
</style>
</head>
<body>
  <header class="site-header">
    <div class="brand"><span class="brand-mark"></span><span class="brand-name">TRANZLY</span></div>
    <nav class="header-actions">
      <span class="icon-btn" aria-label="Menu">
        <svg width="20" height="16" viewBox="0 0 20 16"><rect y="0" width="20" height="3" rx="1.5" fill="#1a1a1a"/><rect y="6.5" width="20" height="3" rx="1.5" fill="#1a1a1a"/><rect y="13" width="20" height="3" rx="1.5" fill="#1a1a1a"/></svg>
      </span>
      <span class="icon-btn" aria-label="Call">
        <svg width="18" height="18" viewBox="0 0 24 24"><path d="M6.6 10.8a15.1 15.1 0 0 0 6.6 6.6l2.2-2.2c.3-.3.7-.4 1-.2 1.1.4 2.3.6 3.6.6.6 0 1 .4 1 1V20c0 .6-.4 1-1 1A17 17 0 0 1 3 4c0-.6.4-1 1-1h3.5c.6 0 1 .4 1 1 0 1.3.2 2.5.6 3.6.1.3 0 .7-.2 1z" fill="#1a1a1a"/></svg>
      </span>
      <span class="icon-btn" aria-label="Search">
        <svg width="20" height="20" viewBox="0 0 20 20"><circle cx="8" cy="8" r="6" fill="none" stroke="#1a1a1a" stroke-width="3"/><line x1="12.5" y1="12.5" x2="18" y2="18" stroke="#1a1a1a" stroke-width="3.2" stroke-linecap="round"/></svg>
      </span>
    </nav>
  </header>

  <section class="hero">
    <h1 class="hero-title">PRIVATE AND BUSINESS</h1>
    <p class="hero-sub">Personalised Transport Service</p>

    <div class="quote-box">
      <h2 class="quote-title">GET INSTANT QUOTE</h2>
      <span class="quote-rule"></span>
      <div class="field origin">Origin (Public Location or Exact Address)</div>
      <div class="field destination">Destination (Public Location or Exact Address)</div>
      <div class="estimate-btn">ESTIMATE FARE</div>
    </div>

    <div class="service corporate">
      <div class="service-photo" role="img" aria-label="Woman driving a car, orange tinted photo"></div>
      <span class="service-name">CORPORATE CARS</span>
    </div>
    <div class="service disability">
      <svg class="pin" width="64" height="66" viewBox="0 0 64 66" aria-hidden="true">
        <path d="M42 0a12 12 0 0 0-12 12c0 9 12 22 12 22s12-13 12-22A12 12 0 0 0 42 0zm0 17a5 5 0 1 1 0-10 5 5 0 0 1 0 10z" fill="#fff"/>
        <path d="M2 52l12-10 14 6 22-6c4-1 6 4 2 6L20 66z" fill="#fff"/>
      </svg>
      <span class="service-name">DISABILITY TRANSIT</span>
    </div>
    <div class="service family small">
      <div class="service-photo" role="img" aria-label="Family with two children at the open boot of a car"></div>
      <span class="service-name">FAMILY TRANSIT SERVICE</span>
    </div>
    <div class="service airport small">
      <div class="service-photo" role="img" aria-label="Travellers with luggage in an airport terminal, orange tinted photo"></div>
      <span class="service-name">AIRPORT TRANSIT</span>
    </div>
  </section>

  <section class="features">
    <div class="feature one">
      <svg width="42" height="36" viewBox="0 0 42 36" aria-hidden="true"><rect x="14" y="0" width="14" height="6" rx="2" fill="none" stroke="#2a2a2a" stroke-width="3"/><rect x="0" y="6" width="42" height="30" rx="4" fill="#2a2a2a"/><rect x="9" y="6" width="2.5" height="30" fill="#fff"/><rect x="30.5" y="6" width="2.5" height="30" fill="#fff"/></svg>
      <p>Nemo enim ipsam voluptatem quia volup tas sit aspernatur aut odit aut fugit, sed quia consequuntur magni dolores.</p>
    </div>
    <div class="feature two">
      <svg width="36" height="36" viewBox="0 0 36 36" aria-hidden="true"><circle cx="18" cy="18" r="15.5" fill="none" stroke="#e07b00" stroke-width="4"/><path d="M18 9v10h-7" fill="none" stroke="#e07b00" stroke-width="3.5"/></svg>
      <p>Nemo enim ipsam voluptatem quia volup tas sit aspernatur aut odit aut fugit, sed quia consequuntur magni dolores.</p>
    </div>
    <div class="feature three">
      <svg width="54" height="36" viewBox="0 0 54 36" aria-hidden="true"><rect x="0" y="0" width="54" height="36" rx="3" fill="#2a2a2a"/></svg>
      <p>Nemo enim ipsam voluptatem quia volup tas sit aspernatur aut odit aut fugit, sed quia consequuntur magni dolores.</p>
    </div>
  </section>

  <footer class="site-footer">Copyrights@ 2017 Tranzly. All Rights Reserved</footer>
</body>
</html>
```